Mastering Modern Vineyard Management

size of the ad - 8”x 10.75" plus 0.25" bleed
I would like an ad for a magazine that will stand out and make people want to read the ad.
The ad should not be crowded and people reading the ad will be able to read the text.
I would like it to be a creative and modern-day design.
the list of topics should not be the focus of the ad.
the text is attached.
If you decide to use people in the ad then please no ladies.
please note that leave over 1 inch for the bottom of the footer

```html
<!DOCTYPE html>
<html lang="en">
<head>
<meta charset="utf-8">
<title>Mastering Modern Vineyard Management – Course Ad</title>
<link rel="stylesheet" href="https://fonts.googleapis.com/css2?family=Antonio:wght@400;500;600;700&family=Barlow:wght@500&display=swap">
<style>
  :root {
    --navy: #0b1a38;
    --gold: #e8c12f;
    --white: #ffffff;
    --ink: #0d0d0d;
    --sky-top: #eef2f5;
    --sky-mid: #b9c9d6;
    --glass: #7f9fb8;
  }
  * { margin: 0; padding: 0; box-sizing: border-box; }
  html, body { width: 907px; height: 1200px; overflow: hidden; background: var(--white); }
  .ad {
    position: relative;
    width: 907px;
    height: 1200px;
    overflow: hidden;
    font-family: "Antonio", "Arial Narrow", sans-serif;
    color: var(--navy);
  }
  .ad__photo, .ad__shapes { position: absolute; inset: 0; width: 907px; height: 1200px; }
  .ad__photo { display: block; }
  .ad__text { position: absolute; white-space: nowrap; }

  .eyebrow { left: 75px; top: 150px; font-size: 44px; font-weight: 700; line-height: 1; }
  .eyebrow__big { display: block; font-size: 72px; line-height: 1; margin-top: 0; }

  .title { left: 78px; top: 296px; font-size: 62px; font-weight: 700; line-height: 71px; text-transform: uppercase; }

  .location { left: 78px; top: 570px; font-size: 76px; font-weight: 700; line-height: 1; color: var(--gold); }
  .details { left: 77px; top: 660px; font-size: 34px; font-weight: 400; line-height: 46px; color: var(--white); }

  .slogan { left: 548px; top: 596px; font-size: 25px; font-weight: 500; line-height: 29px; text-transform: uppercase; }

  .topics { left: 506px; top: 738px; }
  .topics__heading { font-size: 37px; font-weight: 700; line-height: 1; color: var(--ink); margin-bottom: 10px; }
  .topics__heading span { color: var(--gold); }
  .topics__list { list-style: none; font-size: 19px; font-weight: 500; line-height: 26.7px; color: var(--navy); }
  .topics__list li { display: flex; align-items: center; gap: 8px; }
  .topics__list svg { width: 11px; height: 11px; flex: none; }

  .early { left: 77px; top: 902px; }
  .early__heading { font-size: 38px; font-weight: 700; line-height: 1; color: var(--ink); margin-bottom: 18px; }
  .early__body { font-size: 25px; font-weight: 500; line-height: 38px; color: var(--navy); }

  .footer {
    position: absolute; left: 26px; top: 1091px; width: 855px; height: 109px;
    background: var(--ink); color: var(--white);
    display: flex; align-items: center; justify-content: center;
    font-family: "Barlow", Arial, sans-serif; font-weight: 500; font-size: 48px; letter-spacing: 2px;
  }
</style>
</head>
<body>
<main class="ad">
  <svg class="ad__photo" viewBox="0 0 1275 1650" preserveAspectRatio="none" role="img" aria-label="Photograph of a tall glass-fronted office tower against a bright cloudy sky">
    <defs>
      <linearGradient id="sky" x1="0" y1="0" x2="1" y2="1">
        <stop offset="0" stop-color="var(--sky-top)"/>
        <stop offset="0.55" stop-color="var(--sky-mid)"/>
        <stop offset="1" stop-color="var(--glass)"/>
      </linearGradient>
    </defs>
    <rect x="37" y="37" width="1201" height="963" fill="url(#sky)"/>
  </svg>

  <svg class="ad__shapes" viewBox="0 0 1275 1650" preserveAspectRatio="none" aria-hidden="true">
    <path d="M37 37 H197 L272 183 H37 Z" fill="var(--navy)"/>
    <path d="M197 37 H240 L315 183 H272 Z" fill="var(--gold)"/>
    <path d="M37 183 H400 Q430 183 445 210 L515 370 Q525 393 500 393 H37 Z" fill="var(--white)"/>
    <path d="M37 393 H560 Q620 393 650 450 L760 640 Q800 720 880 760 Q1000 805 1238 820 V1000 Q950 960 800 935 Q700 900 640 820 L555 728 H37 Z" fill="var(--gold)"/>
    <path d="M37 728 H555 Q600 800 640 840 Q700 905 752 928 L625 1140 Q590 1208 500 1208 H37 Z" fill="var(--navy)"/>
  </svg>

  <h2 class="ad__text eyebrow">REAL ESTATE<span class="eyebrow__big">COURSE</span></h2>

  <h1 class="ad__text title">Mastering<br>Modern Vineyard<br>Management</h1>

  <p class="ad__text location">LINDEN VALE</p>
  <p class="ad__text details">10 -Tuesday evenings sessions<br>Starting Feb.28<br>Limited Partial Scholarships</p>

  <p class="ad__text slogan">Investing in knowledge<br>is investing in opportunities.</p>

  <section class="ad__text topics">
    <h3 class="topics__heading"><span>TOPICS:</span> PARTIAL LISTING</h3>
    <ul class="topics__list">
      <li><svg viewBox="0 0 12 12"><path d="M1 2 L6 6 L1 10 M6 2 L11 6 L6 10" fill="none" stroke="var(--navy)" stroke-width="2"/></svg>Real estate investment strategies</li>
      <li><svg viewBox="0 0 12 12"><path d="M1 2 L6 6 L1 10 M6 2 L11 6 L6 10" fill="none" stroke="var(--navy)" stroke-width="2"/></svg>Due diligence</li>
      <li><svg viewBox="0 0 12 12"><path d="M1 2 L6 6 L1 10 M6 2 L11 6 L6 10" fill="none" stroke="var(--navy)" stroke-width="2"/></svg>Financing</li>
      <li><svg viewBox="0 0 12 12"><path d="M1 2 L6 6 L1 10 M6 2 L11 6 L6 10" fill="none" stroke="var(--navy)" stroke-width="2"/></svg>Underwriting</li>
      <li><svg viewBox="0 0 12 12"><path d="M1 2 L6 6 L1 10 M6 2 L11 6 L6 10" fill="none" stroke="var(--navy)" stroke-width="2"/></svg>Property management</li>
      <li><svg viewBox="0 0 12 12"><path d="M1 2 L6 6 L1 10 M6 2 L11 6 L6 10" fill="none" stroke="var(--navy)" stroke-width="2"/></svg>Real estate Legal basics</li>
      <li><svg viewBox="0 0 12 12"><path d="M1 2 L6 6 L1 10 M6 2 L11 6 L6 10" fill="none" stroke="var(--navy)" stroke-width="2"/></svg>Sourcing deals</li>
      <li><svg viewBox="0 0 12 12"><path d="M1 2 L6 6 L1 10 M6 2 L11 6 L6 10" fill="none" stroke="var(--navy)" stroke-width="2"/></svg>Syndication</li>
      <li><svg viewBox="0 0 12 12"><path d="M1 2 L6 6 L1 10 M6 2 L11 6 L6 10" fill="none" stroke="var(--navy)" stroke-width="2"/></svg>Dealing with brokers</li>
      <li><svg viewBox="0 0 12 12"><path d="M1 2 L6 6 L1 10 M6 2 L11 6 L6 10" fill="none" stroke="var(--navy)" stroke-width="2"/></svg>Tax fundamentals</li>
    </ul>
  </section>

  <section class="ad__text early">
    <h3 class="early__heading">EARLY BIRD SPECIAL</h3>
    <p class="early__body">For those that started or would like to<br>go into real estate</p>
  </section>

  <footer class="footer">FOOTER 1.25 INCHES</footer>
</main>
</body>
</html>
```